Walk Beside The River

Business Card design

Target Market(s)

People who require support in the commnity

Industry/Entity Type

Mental Health Support

Contact Information for Business Card

Mental Health Support Rosalind Tavener walkbesidetheriver@mailcove.com.au 0481 637 092 PO Box 926 Kallindra Heads QLD 4599

Colors
6B429C
8869AF
B7A5CE
E3DAEB
F3F0F8

Requirements
Must have
• Logo & details listed above
Should not have
• No red or orange

```html
<!DOCTYPE html>
<html lang="en">
<head>
<meta charset="utf-8">
<title>Walk Beside The River – Business Card</title>
<link rel="stylesheet" href="https://fonts.googleapis.com/css2?family=Open+Sans:wght@400;600;700&display=swap">
<style>
  :root {
    --stage: #2b2b2f;
    --card: #1e1e22;
    --card-edge: #141417;
    --purple: #6b429c;
    --purple-text: #7d57b8;
    --lilac: #b7a5ce;
    --yellow: #f2e62a;
    --yellow-shade: #e4d823;
    --white: #ffffff;
    --silver: #8d8d93;
  }
  * { box-sizing: border-box; margin: 0; padding: 0; }
  html, body {
    width: 1200px; height: 780px; overflow: hidden;
    background: var(--stage);
    font-family: "Open Sans", Arial, sans-serif;
  }
  .canvas {
    position: relative; width: 1200px; height: 780px;
    display: flex; align-items: center; justify-content: center; gap: 48px;
  }
  .card {
    position: relative; width: 520px; height: 316px;
    background: var(--card);
    border-radius: 26px;
    overflow: hidden;
    box-shadow: 0 6px 0 var(--card-edge), 0 18px 36px rgba(0,0,0,.45);
  }

  /* Front */
  .brand {
    position: absolute; left: 32px; top: 28px;
    display: flex; align-items: center; gap: 12px;
  }
  .brand-dot { width: 34px; height: 34px; border-radius: 50%; background: var(--purple); }
  .brand-name { color: var(--lilac); font-weight: 600; font-size: 17px; letter-spacing: .04em; }

  .details {
    position: absolute; left: 32px; top: 92px;
    color: var(--white); font-size: 13px; line-height: 1.6;
  }
  .details .service,
  .details .contact-name { font-size: 14px; }
  .details .contact-name { margin-bottom: 4px; }
  .contact-row { display: flex; align-items: center; gap: 9px; }
  .contact-row svg { width: 14px; height: 14px; flex: none; }

  .person { position: absolute; right: 46px; top: 222px; text-align: right; }
  .person-name { font-weight: 700; font-size: 30px; line-height: 1.1; letter-spacing: .01em; }
  .person-name .first { color: var(--yellow); }
  .person-name .last { color: var(--purple-text); }
  .person-role { color: var(--white); font-size: 15px; margin-top: 4px; }

  .edge-steps { position: absolute; right: 0; top: 214px; width: 30px; height: 84px; }

  /* Back */
  .pattern-field {
    position: absolute; inset: 0;
    background: linear-gradient(100deg, #1c1c20 0%, #1f1f23 55%, #4a4a50 80%, var(--silver) 100%);
  }
  .back-brand {
    position: absolute; inset: 0;
    display: flex; align-items: center; justify-content: center;
    color: var(--yellow); font-weight: 700; font-size: 26px; letter-spacing: .03em;
  }
</style>
</head>
<body>
<main class="canvas">

  <section class="card card-front" aria-label="Business card front">
    <div class="brand">
      <span class="brand-dot"></span>
      <span class="brand-name">Walk Beside The River</span>
    </div>

    <div class="details">
      <p class="service">Mental Health Support</p>
      <p class="contact-name">Rosalind Tavener</p>
      <p class="contact-row">
        <svg viewBox="0 0 16 16" aria-hidden="true"><path fill="#f2e62a" d="M4 1.5l2.2 2.6-1.3 1.6a8 8 0 0 0 5.4 5.4l1.6-1.3 2.6 2.2-1.4 2.2C6.8 14 2 9.2 1.8 2.9z"/></svg>
        0481 637 092
      </p>
      <p class="contact-row">
        <svg viewBox="0 0 16 16" aria-hidden="true"><rect x="1.5" y="3.5" width="13" height="9" rx="1.5" fill="none" stroke="#f2e62a" stroke-width="1.6"/><path d="M2 4.5l6 4.5 6-4.5" fill="none" stroke="#f2e62a" stroke-width="1.6"/></svg>
        walkbesidetheriver@mailcove.com.au
      </p>
      <p class="contact-row">
        <svg viewBox="0 0 16 16" aria-hidden="true"><path fill="#f2e62a" d="M8 1a5 5 0 0 0-5 5c0 3.6 5 9 5 9s5-5.4 5-9a5 5 0 0 0-5-5zm0 7a2 2 0 1 1 0-4 2 2 0 0 1 0 4z"/></svg>
        PO Box 926 Kallindra Heads QLD 4599
      </p>
    </div>

    <div class="person">
      <p class="person-name"><span class="first">Marika</span> <span class="last">Delvane</span></p>
      <p class="person-role">CEO/Director</p>
    </div>

    <svg class="edge-steps" viewBox="0 0 30 84" aria-hidden="true">
      <rect x="14" y="0" width="16" height="22" fill="#f2e62a"/>
      <rect x="4" y="20" width="26" height="22" fill="#e4d823"/>
      <rect x="10" y="40" width="20" height="22" fill="#f2e62a"/>
      <rect x="16" y="60" width="14" height="24" fill="#e4d823"/>
    </svg>
  </section>

  <section class="card card-back" aria-label="Business card back">
    <div class="pattern-field" role="img" aria-label="Repeating pattern of small dark stars fading to silver on the right"></div>
    <div class="back-brand">Walk Beside The River</div>
  </section>

</main>
</body>
</html>
```